Corporate Travel Technology Company needs new Business Card design

We need a new business card design to reflect our re-branded company. Our company is called tolvEn (pronounced tolvenn) and we provide Business Intelligence and mobile travel management solutions for the corporate travel industry. Our multinational customers use our solutions to manage large travel budgets and frequent travellers, as well as to save money and reduce risk. We'd like to see designs that use the blue and green palette as well as our corporate logo (attached below). The design should communicate innovation, insight, forward thinking, contemporary, trusted.

Target Market(s)

Large multinational corporates and Travel Agencies.

Industry/Entity Type

Business

Contact Information for Business Card

Rosalind Mercer
Chief Executive
tolvEn
Phone number - +61 (0)2 8134 2907
Email address - rosalind.mercer@tolven-example.com
Mobile number - +61 (0)438 516 702
www.tolven-example.com

Font styles to use
Other font styles liked:
• Please use font as close to corporate logo as possible

Colors
0255a3
0393ce
00a990
33b8a4
33a6d7
3176b5

Requirements
Must have
• Please include the words;
• Mobile Travel Management
• Accelerating Travel Business Insights
• Use corporate logo - although icon can be stylised if needed

```html
<!DOCTYPE html>
<html lang="en">
<head>
<meta charset="utf-8">
<title>tolvEn business card</title>
<link rel="stylesheet" href="https://fonts.googleapis.com/css2?family=Open+Sans:wght@400;600&display=swap">
<style>
  :root {
    --page: #e9ecee;
    --card: #ffffff;
    --sky: #33a6d7;
    --teal: #00a990;
    --teal-light: #33b8a4;
    --slate: #4b5f5d;
    --slate-dark: #3d4e4c;
  }
  * { margin: 0; padding: 0; box-sizing: border-box; }
  html, body { width: 1200px; height: 902px; overflow: hidden; }
  body {
    background: var(--page);
    font-family: "Open Sans", Arial, sans-serif;
    display: flex;
    flex-direction: column;
    align-items: center;
    justify-content: center;
    gap: 40px;
  }
  .card {
    position: relative;
    width: 700px;
    height: 400px;
    background: var(--card);
    overflow: hidden;
    box-shadow: 0 4px 18px rgba(0,0,0,0.12);
  }
  .card-art { position: absolute; inset: 0; width: 100%; height: 100%; }

  .wordmark {
    display: flex;
    align-items: center;
    gap: 14px;
    font-weight: 400;
    letter-spacing: -1px;
    line-height: 1;
  }
  .wordmark-dot { border-radius: 50%; flex: none; }

  /* back */
  .brand-block {
    position: absolute;
    left: 50%; top: 50%;
    transform: translate(-50%, -50%);
    display: flex;
    flex-direction: column;
    align-items: center;
    text-align: center;
  }
  .card-back .wordmark { font-size: 110px; color: var(--sky); }
  .card-back .wordmark-dot { width: 42px; height: 42px; border: 7px solid var(--teal); }
  .tagline-main {
    margin-top: 10px;
    font-size: 24px;
    font-weight: 600;
    color: var(--teal);
    letter-spacing: 0.5px;
  }
  .tagline-sub {
    margin-top: 4px;
    font-size: 17px;
    font-weight: 400;
    color: var(--slate);
    letter-spacing: 0.5px;
  }

  /* front */
  .card-front .wordmark {
    position: absolute;
    right: 150px; top: 38px;
    font-size: 80px;
    color: var(--slate);
  }
  .card-front .wordmark-dot { width: 30px; height: 30px; border: 5px solid var(--teal); }

  .holder {
    position: absolute;
    left: 42px; bottom: 38px;
    color: var(--slate-dark);
  }
  .holder-name { font-size: 34px; font-weight: 600; line-height: 1.1; }
  .holder-title { font-size: 23px; font-weight: 400; margin-top: 2px; }

  .contacts {
    position: absolute;
    right: 26px; bottom: 40px;
    padding-left: 12px;
    border-left: 2px solid var(--slate-dark);
    list-style: none;
    color: var(--slate-dark);
    font-size: 15px;
  }
  .contacts li { display: flex; align-items: center; gap: 10px; height: 26px; }
  .contact-icon {
    width: 18px; height: 18px;
    background: var(--slate-dark);
    border-radius: 2px;
    display: flex; align-items: center; justify-content: center;
    flex: none;
  }
  .contact-icon svg { width: 12px; height: 12px; }
</style>
</head>
<body>

  <section class="card card-back" aria-label="Card back">
    <svg class="card-art" viewBox="0 0 700 400" aria-hidden="true">
      <circle cx="350" cy="200" r="335" fill="none" stroke="var(--slate)" stroke-width="44"/>
    </svg>
    <div class="brand-block">
      <div class="wordmark"><span class="wordmark-dot"></span>tolvEn</div>
      <p class="tagline-main">Mobile Travel Management</p>
      <p class="tagline-sub">Accelerating Travel Business Insights</p>
    </div>
  </section>

  <section class="card card-front" aria-label="Card front">
    <svg class="card-art" viewBox="0 0 700 400" aria-hidden="true">
      <path d="M0,262 C250,300 560,250 700,40 L700,400 L0,400 Z" fill="var(--sky)"/>
      <path d="M50,250 C280,290 580,234 692,28 C585,244 280,288 50,256 Z" fill="var(--teal)"/>
    </svg>

    <div class="wordmark"><span class="wordmark-dot"></span>tolvEn</div>

    <div class="holder">
      <p class="holder-name">Rosalind Mercer</p>
      <p class="holder-title">Chief Executive</p>
    </div>

    <ul class="contacts">
      <li>
        <span class="contact-icon"><svg viewBox="0 0 12 12"><path d="M1,3 Q6,0 11,3 L10,5 L8,4.5 L8,3.5 Q6,3 4,3.5 L4,4.5 L2,5 Z M3,6 H9 L10,10 H2 Z" fill="#fff"/></svg></span>
        +61 (0)2 8134 2907
      </li>
      <li>
        <span class="contact-icon"><svg viewBox="0 0 12 12"><rect x="3.5" y="1" width="5" height="10" rx="1" fill="none" stroke="#fff" stroke-width="1.3"/><circle cx="6" cy="9" r="0.7" fill="#fff"/></svg></span>
        +61 (0)438 516 702
      </li>
      <li>
        <span class="contact-icon"><svg viewBox="0 0 12 12"><g fill="none" stroke="#fff" stroke-width="1"><circle cx="6" cy="6" r="4.5"/><ellipse cx="6" cy="6" rx="2" ry="4.5"/><path d="M1.5,6 H10.5"/></g></svg></span>
        www.tolven-example.com
      </li>
      <li>
        <span class="contact-icon"><svg viewBox="0 0 12 12"><g fill="none" stroke="#fff" stroke-width="1.1"><rect x="1.5" y="3" width="9" height="6.5"/><path d="M1.5,3 L6,7 L10.5,3"/></g></svg></span>
        rosalind.mercer@tolven-example.com
      </li>
    </ul>
  </section>

</body>
</html>
```